colour pencil case design

I am looking for a design for the front of a pencil case. The pencil case has 2 versions, 1 white fabric and 1 black fabric. The design should have 2 versions, eg. white word on black fabric and black words on white fabric. Its for children and teenagers’ aged 7 to 18. I can have 2 separate designs.
The pencil case is 22cm by 14cm. So the size of the image should be 18cm by 11cm. Files should be in png format and already in the correct size.
It must have the word “Believe”in big size. The letter b can be in capps or small letter. Prefer the font used in
I am looking for a background or image that can represent the phrase. If the design is good, I am open to also black and white theme.
Can also be black and white or colour... I have attached the font that I like for the main word "Believe". https://www.quillnest.net/gallery/583047192/Free-Font-Corvena-Modern-Script. Or you can use this font for the word Believe as well…. "Playlist script
Besides the word Believe, you should have the sentence ‘you can and you will”. It can be all in capps or small letter. (smaller size and different font from your word.
Target Market(s)
children and teenagers
Industry/Entity Type
tuition
Requirements
Must have
- The word Believe and the phrase I can and I will
Nice to have
- Some colourful pictures that can represent the phrase

```html
<!DOCTYPE html>
<html lang="en">
<head>
<meta charset="UTF-8">
<title>Believe – Pencil Case Front, Light and Dark Versions</title>
<link rel="stylesheet" href="https://fonts.googleapis.com/css2?family=Dancing+Script:wght@700&family=Montserrat:wght@400&display=swap">
<style>
  :root {
    --page: #ffffff;
    --ink: #0c0c0c;
    --paper: #f4f4f4;
    --charcoal: #1a1a1a;
    --chalk: #e6e6e6;
    --rule-light: #c9c9c9;
    --rule-dark: #6a6a6a;
    --shadow: rgba(0, 0, 0, 0.35);
  }
  * { margin: 0; padding: 0; box-sizing: border-box; }
  html, body {
    width: 997px;
    height: 1200px;
    overflow: hidden;
    background: var(--page);
  }
  .sheet {
    position: relative;
    width: 997px;
    height: 1200px;
  }
  .case-front {
    position: absolute;
    left: 72px;
    width: 858px;
    height: 524px;
    overflow: hidden;
    box-shadow: 6px 6px 6px var(--shadow);
  }
  .case-front--light { top: 50px; background: var(--paper); color: var(--ink); }
  .case-front--dark  { top: 619px; background: var(--charcoal); color: var(--page); }

  .brush-edges,
  .headline {
    position: absolute;
    inset: 0;
    width: 100%;
    height: 100%;
  }
  .case-front--light .brush-edges { fill: var(--ink); }
  .case-front--dark  .brush-edges { fill: var(--chalk); }

  .headline-word {
    font-family: "Dancing Script", cursive;
    font-weight: 700;
    font-size: 310px;
    fill: currentColor;
  }
  .tagline {
    position: absolute;
    left: 460px;
    top: 338px;
    font-family: "Montserrat", sans-serif;
    font-size: 20px;
    letter-spacing: 0.5px;
    white-space: nowrap;
  }
  .rule {
    position: absolute;
    height: 1px;
    top: 382px;
  }
  .case-front--light .rule { left: 198px; width: 450px; background: var(--rule-light); }
  .case-front--dark  .rule { left: 82px;  width: 698px; background: var(--rule-dark); }
</style>
</head>
<body>
<main class="sheet">

  <section class="case-front case-front--light">
    <svg class="brush-edges" viewBox="0 0 858 524" role="img" aria-label="Black dry-brush paint strokes framing the corners and right edge">
      <path d="M0 0 H170 L150 14 L110 22 L70 46 L30 70 L0 96 Z"/>
      <path d="M446 0 H540 L520 12 L490 26 L470 30 L450 18 Z"/>
      <path d="M858 0 V524 H690 L720 500 L760 480 L790 440 L805 390 L800 330 L815 270 L810 200 L820 140 L805 80 L812 30 L790 0 Z"/>
      <path d="M0 524 V440 L30 452 L70 470 L110 490 L130 510 L120 524 Z"/>
    </svg>
    <svg class="headline" viewBox="0 0 858 524">
      <title>Believe</title>
      <text class="headline-word" x="84" y="318" textLength="690" lengthAdjust="spacingAndGlyphs">Believe</text>
    </svg>
    <p class="tagline">YOU CAN AND YOU WILL</p>
    <div class="rule"></div>
  </section>

  <section class="case-front case-front--dark">
    <svg class="brush-edges" viewBox="0 0 858 524" role="img" aria-label="White dry-brush paint strokes framing the corners and right edge">
      <path d="M0 0 H170 L150 14 L110 22 L70 46 L30 70 L0 96 Z"/>
      <path d="M446 0 H540 L520 12 L490 26 L470 30 L450 18 Z"/>
      <path d="M858 0 V524 H690 L720 500 L760 480 L790 440 L805 390 L800 330 L815 270 L810 200 L820 140 L805 80 L812 30 L790 0 Z"/>
      <path d="M0 524 V440 L30 452 L70 470 L110 490 L130 510 L120 524 Z"/>
    </svg>
    <svg class="headline" viewBox="0 0 858 524">
      <title>Believe</title>
      <text class="headline-word" x="84" y="318" textLength="690" lengthAdjust="spacingAndGlyphs">Believe</text>
    </svg>
    <p class="tagline">YOU CAN AND YOU WILL</p>
    <div class="rule"></div>
  </section>

</main>
</body>
</html>
```